New Fun, Positive, energised looking Business Card Needed for High Achiever Coach

I am looking for a two sided full colour business card. I am self employed and have recently re branded my 1-2-1 work Re-Energising Busy Leaders. My target client base for these cards is therefore high achievers - usually aged 40 -55, they are often entrepreneurs, CEO or work in banking and finance and 2/3 are male. I work with them on 90 day or 6 month coaching programs to help them live their success in a healthier, more sustainable and fulfiiled way. They pay for this privately so though they are corporate types the cards need not look 'corporate'. I want to portray the idea of transformation, vitality and re-connecting.
You can get a feel for the look I like on my new website: morvenlisk.co.uk
I want to use this logo with strapline (Re-Energising Busy Leaders) (I purchased off Logoharbor) and font/ colours (the turquoise and green).
Details to include on the card:
www.morvenlisk.co.uk
+44 7915 302618
morven@morvenlisk.co.uk
skype: morvenlisk
I'd also like to include:
Do you struggle to switch off? Want to be healthier and feel fitter? Want closer relationships? More clarity over the direction you are headed? I can help you do these things using integrated mind-body techniques. Visit morvenlisk.co.uk TODAY to apply for a FREE Breakthrough session.
BUT if that is too much text for a card I am open to advice/ammendments.
Updates
Thanks for your design - I am considering them. PLease change the wording to :

```html
<!DOCTYPE html>
<html lang="en">
<head>
<meta charset="utf-8">
<title>Morven Lisk – Business Card</title>
<link href="https://fonts.googleapis.com/css2?family=Open+Sans:wght@400;600;800&display=swap" rel="stylesheet">
<style>
  :root {
    --turquoise: #1aa3cc;
    --green: #5cb85c;
    --ink: #3c3c3c;
    --paper: #ffffff;
    --backdrop: #e9e9e9;
    --divider: #cfcfcf;
  }
  * { box-sizing: border-box; margin: 0; padding: 0; }
  html, body {
    width: 1200px; height: 720px; overflow: hidden;
    background: var(--backdrop);
    font-family: "Open Sans", Arial, sans-serif;
  }
  .sheet {
    position: relative; width: 1200px; height: 720px;
    display: flex; align-items: center; justify-content: center; gap: 40px;
  }
  .card {
    position: relative; width: 540px; height: 320px;
    background: var(--paper);
    box-shadow: 0 6px 18px rgba(0,0,0,0.12);
    overflow: hidden;
  }

  /* brand lockup */
  .brand { display: flex; flex-direction: column; align-items: center; }
  .brand-name {
    display: flex; align-items: center; gap: 10px;
    color: var(--turquoise); font-weight: 800; font-size: 32px; line-height: 1;
    white-space: nowrap;
  }
  .brand-dot {
    width: 20px; height: 20px; border-radius: 50%; background: var(--green); flex: none;
  }
  .brand-strap {
    margin-top: 6px; color: var(--turquoise);
    font-size: 13px; font-weight: 600; white-space: nowrap;
  }

  /* front */
  .card-front .front-top {
    height: 196px; display: flex; align-items: flex-end; justify-content: center;
    padding-bottom: 26px;
  }
  .card-front .front-rule { height: 3px; background: var(--green); }
  .card-front .contact-band {
    position: absolute; left: 0; right: 0; bottom: 0; height: 121px;
    background: var(--turquoise);
    display: flex; align-items: center; justify-content: center;
    color: var(--paper); font-size: 15px;
  }
  .contact-col { display: flex; flex-direction: column; gap: 12px; }
  .contact-col.left { align-items: flex-end; padding-right: 16px; }
  .contact-col.right { align-items: flex-start; padding-left: 16px; }
  .contact-split { width: 1px; height: 62px; background: rgba(255,255,255,0.7); }
  .contact-item { display: flex; align-items: center; gap: 7px; white-space: nowrap; }
  .contact-item svg { width: 15px; height: 15px; flex: none; }
  .handle-dot { width: 13px; height: 13px; border-radius: 50%; background: var(--paper); flex: none; }

  /* back */
  .card-back { display: flex; align-items: center; }
  .card-back .back-brand { width: 214px; display: flex; justify-content: center; padding-top: 40px; }
  .card-back .back-brand .brand-name { font-size: 25px; gap: 8px; }
  .card-back .back-brand .brand-dot { width: 16px; height: 16px; }
  .card-back .back-brand .brand-strap { font-size: 11px; }
  .back-split { width: 1px; height: 230px; background: var(--divider); flex: none; }
  .pitch {
    flex: 1; padding: 0 14px 0 16px;
    color: var(--ink); font-size: 12px; line-height: 1.55;
  }
  .pitch p + p { margin-top: 10px; }
  .pitch .nowrap { white-space: nowrap; }
  .pitch strong { font-weight: 800; }
</style>
</head>
<body>
<main class="sheet">

  <section class="card card-front" aria-label="Business card front">
    <div class="front-top">
      <div class="brand">
        <div class="brand-name"><span class="brand-dot"></span>Morven Lisk</div>
        <div class="brand-strap">Re-Energising Busy Leaders</div>
      </div>
    </div>
    <div class="front-rule"></div>
    <div class="contact-band">
      <div class="contact-col left">
        <div class="contact-item">
          <svg viewBox="0 0 16 16" aria-hidden="true"><circle cx="8" cy="8" r="7.5" fill="#fff"/><path d="M5.2 4.2l1.6-.3.8 2-1 .8c.5 1.1 1.4 2 2.5 2.5l.8-1 2 .8-.3 1.6c-3.6.2-6.6-2.8-6.4-6.4z" fill="#1aa3cc"/></svg>
          <span>+44 7915 302618</span>
        </div>
        <div class="contact-item">
          <svg viewBox="0 0 16 16" aria-hidden="true"><circle cx="8" cy="8" r="7.5" fill="#fff"/><rect x="4" y="5.2" width="8" height="5.6" fill="#1aa3cc"/><path d="M4 5.2l4 3 4-3" stroke="#fff" stroke-width="0.9" fill="none"/></svg>
          <span>morven@morvenlisk.co.uk</span>
        </div>
      </div>
      <div class="contact-split"></div>
      <div class="contact-col right">
        <div class="contact-item">
          <svg viewBox="0 0 16 16" aria-hidden="true"><circle cx="8" cy="8" r="7.5" fill="#fff"/><circle cx="8" cy="8" r="4.5" fill="none" stroke="#1aa3cc" stroke-width="1"/><ellipse cx="8" cy="8" rx="2" ry="4.5" fill="none" stroke="#1aa3cc" stroke-width="1"/><path d="M3.5 8h9" stroke="#1aa3cc" stroke-width="1"/></svg>
          <span>www.morvenlisk.co.uk</span>
        </div>
        <div class="contact-item">
          <span class="handle-dot"></span>
          <span>morvenlisk</span>
        </div>
      </div>
    </div>
  </section>

  <section class="card card-back" aria-label="Business card back">
    <div class="back-brand">
      <div class="brand">
        <div class="brand-name"><span class="brand-dot"></span>Morven Lisk</div>
        <div class="brand-strap">Re-Energising Busy Leaders</div>
      </div>
    </div>
    <div class="back-split"></div>
    <div class="pitch">
      <p>Do you struggle to switch off?<br>Want to be healthier and feel fitter?<br>Want closer relationships?<br><span class="nowrap">More clarity over the direction you are headed?</span></p>
      <p>I can help you do these things using integrated<br>mind-body techniques.</p>
      <p>Visit <strong>morvenlisk.co.uk</strong> TODAY to apply for a<br>FREE Breakthrough session.</p>
    </div>
  </section>

</main>
</body>
</html>
```